Landscape Company in need of logo and business card update. Current logo file is attached.

I need a business card design for a Woman Owned Landscape business in Kansas City. I do Native plant installation and maintenance as well as mowing, chemical applications and residential and commercial landscaping.
My colors are navy, green and white.
I currently have a logo that can be used or you can redesign it.

Target Market(s)

Residential and commercial

Industry/Entity Type

Landscape

Contact Information for Business Card

On back of current card it lists what I do and website:
BMP/Raingarden Maintenance and Installation, Certified Chemical Applicator for Trees, shrubs, and turf; Landscape Design and Installation for residential and commercial.

Logo Text

Brookfern Landscape Works, LLC

Font styles to use
Other font styles liked:
• See current font on logo examples

Requirements
Must have
• Phone number: 913-555-0182
• Website: www.brookfernyards.example
• Colors: Navy, Green, white
• Email: brookfernyards@mailbox.example
• Address: PO BOX 472108 Fernhollow, KS 66999
• Name of Person: Marcy Delgado, owner

```html
<!DOCTYPE html>
<html lang="en">
<head>
<meta charset="utf-8">
<title>Brookfern Landscape Works – Business Card</title>
<link href="https://fonts.googleapis.com/css2?family=Roboto+Condensed:wght@300;400;700&display=swap" rel="stylesheet">
<style>
  :root {
    --backdrop: #ededed;
    --paper: #f9f9f9;
    --green: #1dbd6e;
    --navy: #3a4470;
    --navy-deep: #24406a;
    --accent-red: #e0474c;
  }
  * { box-sizing: border-box; margin: 0; padding: 0; }
  html, body {
    width: 1200px; height: 778px; overflow: hidden;
    background: var(--backdrop);
    font-family: "Roboto Condensed", "Arial Narrow", sans-serif;
  }
  .card {
    position: absolute;
    top: 65px;
    width: 370px; height: 648px;
    background: var(--paper);
    box-shadow: 0 10px 30px rgba(0,0,0,0.12);
  }
  .card--front { left: 190px; }
  .card--back { left: 640px; }

  .brand {
    position: absolute; left: 30px; top: 32px;
    display: flex; align-items: center; gap: 12px;
  }
  .brand__dot {
    width: 40px; height: 40px; border-radius: 50%;
    background: var(--accent-red); flex: none;
  }
  .brand__name {
    font-weight: 400; font-size: 14px; letter-spacing: 0.04em;
    color: var(--navy-deep); text-transform: uppercase; line-height: 1.3;
    width: 150px;
  }

  .person { position: absolute; left: 30px; top: 318px; }
  .person__name {
    font-size: 40px; line-height: 1; color: var(--green);
    font-weight: 300; letter-spacing: -0.01em;
  }
  .person__name strong { font-weight: 700; }
  .person__role {
    margin-top: 6px; font-size: 15px; font-weight: 300; color: var(--green);
  }

  .contact { position: absolute; left: 30px; top: 500px; list-style: none; }
  .contact li {
    display: flex; align-items: center; gap: 12px;
    font-size: 15px; font-weight: 300; color: var(--navy);
    height: 28px; white-space: nowrap;
  }
  .contact svg { width: 14px; height: 14px; flex: none; }

  .back-mark {
    position: absolute; left: 50%; top: 150px; transform: translateX(-50%);
    display: flex; flex-direction: column; align-items: center; gap: 14px;
    width: 300px;
  }
  .back-mark__dot {
    width: 130px; height: 130px; border-radius: 50%; background: var(--accent-red);
  }
  .back-mark__name {
    font-size: 16px; letter-spacing: 0.06em; text-transform: uppercase;
    color: var(--navy-deep); text-align: center;
  }
  .services {
    position: absolute; left: 30px; right: 30px; top: 370px;
    text-align: center; font-size: 13px; font-weight: 300; line-height: 1.5;
    color: var(--navy);
  }
  .back-web {
    position: absolute; left: 0; right: 0; bottom: 50px;
    text-align: center; font-size: 14px; font-weight: 300; color: var(--navy);
  }
</style>
</head>
<body>
  <section class="card card--front">
    <div class="brand">
      <span class="brand__dot"></span>
      <span class="brand__name">Brookfern Landscape Works, LLC</span>
    </div>

    <div class="person">
      <h1 class="person__name">Marcy <strong>DELGADO</strong></h1>
      <p class="person__role">Owner</p>
    </div>

    <ul class="contact">
      <li>
        <svg viewBox="0 0 14 14" fill="none" stroke="var(--green)" stroke-width="1.2"><path d="M7 13s4-4.3 4-7.2A4 4 0 0 0 3 5.8C3 8.7 7 13 7 13z"/><circle cx="7" cy="5.8" r="1.5"/></svg>
        PO BOX 472108 Fernhollow, KS 66999
      </li>
      <li>
        <svg viewBox="0 0 14 14" fill="none" stroke="var(--green)" stroke-width="1.2"><path d="M3 1.5l2.2 2.3-1.2 1.6a8 8 0 0 0 4.6 4.6l1.6-1.2 2.3 2.2-1.5 1.5C6.5 12.5 1.5 7.5 1.5 3z"/></svg>
        913-555-0182
      </li>
      <li>
        <svg viewBox="0 0 14 14" fill="none" stroke="var(--green)" stroke-width="1.2"><rect x="1.5" y="3" width="11" height="8"/><path d="M1.5 3L7 8l5.5-5"/></svg>
        brookfernyards@mailbox.example
      </li>
      <li>
        <svg viewBox="0 0 14 14" fill="none" stroke="var(--green)" stroke-width="1.2"><circle cx="7" cy="7" r="2.2"/><path d="M9.2 5v2.8c0 1.5 2.8 1.5 2.8-.8A5 5 0 1 0 9.5 11.3"/></svg>
        www.brookfernyards.example
      </li>
    </ul>
  </section>

  <section class="card card--back">
    <div class="back-mark">
      <span class="back-mark__dot"></span>
      <span class="back-mark__name">Brookfern Landscape Works, LLC</span>
    </div>
    <p class="services">
      BMP/Raingarden Maintenance and Installation<br>
      Certified Chemical Applicator for Trees, Shrubs, and Turf<br>
      Landscape Design and Installation<br>
      for residential and commercial
    </p>
    <p class="back-web">www.brookfernyards.example</p>
  </section>
</body>
</html>
```